Building company buisness cards

We are looking for a sharp modern new look for our business cards.
We are a New Zealand based company that specialises in house and land packages.
We have attached a photo of the current logo and would like to see if it can be improved somehow if needed.
We are open to any colours but we have chosen green at this stage.
Feel free to change the font and make the logo smarter looking.
Play with the colours and see what looks best.

We want a card that looks so good know one will want to throw it away!

Target Market(s)

Home buyers

Industry/Entity Type

Building

Contact Information for Business Card

Derek Tolvane
0217394062
dtolvane@quillmarkhomesteads.co.nz
quillmarkhomesteads.co.nz

Font styles to use
Serif
Sans Serif

Colors

Designer to choose colors to be used in the design.

Requirements
Must have
• Logo and company name on one side, details on the other side
Nice to have
• Color codes for the original green are HEX #4a8028, RGB(74,128,40), CMYK(42,0,69,50)
• Round corners, Raised and/or spot UV

```html
<!DOCTYPE html>
<html lang="en">
<head>
<meta charset="utf-8">
<title>Quillmark Homesteads – Business Cards</title>
<link rel="stylesheet" href="https://fonts.googleapis.com/css2?family=Arimo:wght@700&family=PT+Sans:wght@400&display=swap">
<style>
  :root {
    --backdrop: #c8c9cb;
    --card: #ffffff;
    --brand-green: #4a8028;
    --swoosh-grey: #6b6b6b;
    --ink: #1e1e1e;
    --on-green: #ffffff;
    --tint-green: #e6efdf;
  }
  * { margin: 0; padding: 0; box-sizing: border-box; }
  html, body {
    width: 1200px; height: 1015px; overflow: hidden;
    background: var(--backdrop);
  }
  .canvas { position: relative; width: 1200px; height: 1015px; }
  .card {
    position: absolute;
    width: 687px; height: 393px;
    border-radius: 30px;
    background: var(--card);
    overflow: hidden;
    box-shadow: 0 3px 8px rgba(0,0,0,0.28);
  }
  .card--front { left: 79px; top: 85px; }
  .card--back  { left: 435px; top: 544px; }
  .card svg.swoosh { position: absolute; inset: 0; }

  .wordmark {
    position: absolute;
    font-family: "Arimo", Arial, sans-serif;
    font-weight: 700;
    color: var(--brand-green);
    text-align: center;
    line-height: 1;
    letter-spacing: -0.5px;
  }
  .wordmark__top { display: block; }
  .wordmark__bottom { display: block; }
  .wordmark-rule {
    position: absolute; height: 1.5px; background: var(--brand-green);
  }
  .brand-dot {
    position: absolute; border-radius: 50%; background: var(--brand-green);
  }

  /* front */
  .card--front .brand-dot { left: 183px; top: 30px; width: 26px; height: 26px; }
  .card--front .wordmark { left: 20px; top: 78px; width: 354px; }
  .card--front .wordmark__top { font-size: 26px; }
  .card--front .wordmark__bottom { font-size: 38px; margin-top: 4px; }
  .card--front .wordmark-rule { left: 124px; top: 198px; width: 132px; }
  .holder-name {
    position: absolute; left: 41px; top: 244px;
    font-family: "Arimo", Arial, sans-serif; font-weight: 700;
    font-size: 26px; color: var(--brand-green);
  }
  .contact-list {
    position: absolute; right: 18px; top: 285px;
    list-style: none;
    font-family: "PT Sans", "Myriad Pro", sans-serif;
    font-size: 17px; color: var(--on-green);
  }
  .contact-list li {
    display: flex; align-items: center; justify-content: flex-end;
    height: 29px; gap: 10px;
  }
  .contact-list svg { width: 16px; height: 16px; flex: none; }

  /* back */
  .brand-field {
    position: absolute; left: 40px; top: 30px;
    width: 330px; height: 330px; border-radius: 50%;
    background: var(--tint-green);
  }
  .card--back .wordmark { left: 380px; top: 266px; width: 290px; }
  .card--back .wordmark__top { font-size: 25px; }
  .card--back .wordmark__bottom { font-size: 34px; margin-top: 3px; }
  .card--back .wordmark-rule { left: 464px; top: 344px; width: 109px; }
  .back-url {
    position: absolute; right: 14px; top: 358px;
    font-family: "PT Sans", "Myriad Pro", sans-serif;
    font-size: 17px; color: var(--ink);
  }
  .back-url .url-name { color: var(--brand-green); }
</style>
</head>
<body>
<main class="canvas">

  <section class="card card--front" aria-label="Card front">
    <svg class="swoosh" viewBox="0 0 687 393" width="687" height="393" aria-hidden="true">
      <path d="M0,288 C70,335 190,350 290,318 C370,292 430,255 484,216 C420,262 345,305 260,330 C170,352 70,345 0,312 Z" fill="var(--swoosh-grey)"/>
      <path d="M0,334 C70,362 190,368 300,338 C450,296 600,170 687,14 L687,393 L0,393 Z" fill="var(--brand-green)"/>
    </svg>

    <span class="brand-dot" aria-hidden="true"></span>
    <div class="wordmark">
      <span class="wordmark__top">quillmark</span>
      <span class="wordmark__bottom">homesteads.</span>
    </div>
    <span class="wordmark-rule"></span>

    <p class="holder-name">Derek Tolvane</p>

    <ul class="contact-list">
      <li>0217394062
        <svg viewBox="0 0 16 16"><circle cx="8" cy="8" r="7" fill="none" stroke="#fff" stroke-width="1.3"/><path d="M6 4.5 L7.3 6.5 L6.6 7.3 C7 8.3 7.7 9 8.7 9.4 L9.5 8.7 L11.5 10 L10.6 11.5 C7.5 11.2 4.8 8.5 4.5 5.4 Z" fill="#fff"/></svg>
      </li>
      <li>dtolvane@quillmarkhomesteads.co.nz
        <svg viewBox="0 0 16 16"><rect x="1" y="5" width="14" height="9" fill="#fff"/><path d="M1 5 L8 10 L15 5" fill="none" stroke="var(--brand-green)" stroke-width="1.2"/><path d="M3 5 L8 1.5 L13 5" fill="none" stroke="#fff" stroke-width="1.2"/></svg>
      </li>
      <li>www.quillmarkhomesteads.co.nz
        <svg viewBox="0 0 16 16" fill="none" stroke="#fff" stroke-width="1"><circle cx="8" cy="8" r="7"/><ellipse cx="8" cy="8" rx="3" ry="7"/><line x1="1" y1="8" x2="15" y2="8"/><path d="M2.3 4.5 H13.7 M2.3 11.5 H13.7"/></svg>
      </li>
    </ul>
  </section>

  <section class="card card--back" aria-label="Card back">
    <div class="brand-field" role="img" aria-label="Brand emblem area"></div>
    <div class="wordmark">
      <span class="wordmark__top">quillmark</span>
      <span class="wordmark__bottom">homesteads.</span>
    </div>
    <span class="wordmark-rule"></span>
    <p class="back-url">www.<span class="url-name">quillmarkhomesteads</span>.co.nz</p>
  </section>

</main>
</body>
</html>
```